Need a clean & modern homepage for an education site + opportunity for longer term work

Thanks for viewing our project. We are excited about this new website and we hope that we might build a relationship with designers as we work on this project. I provided quite a few details and requirements to help you more quickly create a design that meets our needs.
Who we are:
We are a website that discusses the importance of college accreditation and provides a directory of college programs.
What we need:
A homepage that meets the below requirements and is inspired by the examples provided
Definition of accredited:
ac·cred·it·ed [uh-kred-i-tid] adj.
1. officially recognized as meeting the essential requirements, as of academic excellence: accredited schools.
2. provided with official credentials, as by a government: an accredited diplomatic representative.
3. accepted as authoritative: an accredited theory.
Overall look and feel for the homepage:
- Clean, simple and modern
- Limited (or zero) pictures
- Utilize color blocks with text
- A trend seems to be longer vertical length homepages with lots of whitespace. I generally like this trend as long as the page is not way to tall.
Inspirations: Sites that have a similar look and feel to what I need.
http://lernvoxa.org/
http://www.campusmetrik.com/colleges/brantmoor-university/
http://quietfolding.org/
http://www.velostrahiring.com/
http://www.zunq.com/
http://sketches.bxv.com/
Items to be included on the homepage. Details below on each item.
- Top navigation
- Logo: Please leave a blank area for a logo. The logo has not been designed.
- Simple graphic/color block at the top that highlights a definition of “Accredited” – the definition should be formatted like it is being copy/pasted from a dictionary.
- Space for a video and small (50 word) written description of the video. You can use placeholder text.
- One section with 3 Paragraphs of content (each paragraph around 100 words) with a header at the top. You can use placeholder text but please create the formatting. At the end of the 3 paragraphs please have a “Read More” Note this shouldn't be 3 separate paragraphs with three read mores - it is 3 paragraphs with one read more at the end.
- An area with the header “Search Colleges by State” that has anchor text links to all 50 states.
Top navigation:
- Home
- States – with a subnav dropdown that includes all 50 US states.
- Programs – with a subnav dropdown that includes program titles (list below)
- Degrees - with a subnav dropdown that includes 5 degree levels (list below)
- Accreditation – no subnav
- Rankings – no subnav
- Resources – no subnav
Footer
- Link to about us, privacy, and a copyright www.url.com
Programs List for sub navigation
Accounting
Art
Bible
Business
Criminal Justice
Design
Education
Engineering
English
Law
LPN to RN
Management
Math
MBA
MPH
Medical Assisting
Military
Nursing
Occupational Therapy
Paralegal
Psychology
Pharmacy
RN to BSN
Radiology
Social Work
Sonography
Degrees list for sub navigation
Certificate
Associate
Bachelors
Masters
PhD
Thanks so much - looking forward to working with you!
Education

```html
<!DOCTYPE html>
<html lang="en">
<head>
<meta charset="utf-8">
<title>My Website — College Accreditation Directory</title>
<link rel="stylesheet" href="https://fonts.googleapis.com/css2?family=Questrial&family=Mulish:wght@400;700;800&display=swap">
<style>
:root{
  --white:#ffffff;
  --ink:#1d2b4a;
  --nav-grey:#9aa3ad;
  --top-line:#2a9fd8;
  --hero-sky:#8fc4e4;
  --hero-deep:#3a7eb3;
  --banner:#1d5c8f;
  --accent-blue:#1ca6e2;
  --green:#4dbf60;
  --paper:#eeeeee;
  --card-text:#555b63;
  --sky:#30bde0;
  --sky-dark:#2aa6c8;
  --mid-blue:#1b84c6;
  --deep-blue:#175e95;
  --state-btn:#5a95c4;
  --map:#6fa5d3;
}
*{box-sizing:border-box;margin:0;padding:0}
html,body{width:1200px;height:2462px;overflow:hidden}
body{position:relative;background:var(--white);font-family:"Questrial",sans-serif;color:var(--ink)}
.abs{position:absolute}

/* header */
.topbar{left:0;top:0;width:1200px;height:92px;background:var(--white);border-top:6px solid var(--top-line);z-index:3}
.brand{left:98px;top:38px;font-family:"Mulish",sans-serif;font-weight:700;font-size:23px;color:var(--ink);letter-spacing:.5px}
.nav a{position:absolute;top:50px;font-size:18px;color:var(--nav-grey);text-decoration:none}
.social span{position:absolute;top:22px;width:24px;height:24px;border-radius:50%;background:var(--green)}

/* hero */
.hero{left:0;top:92px;width:1200px;height:438px;background:linear-gradient(180deg,var(--hero-sky) 0%,#6aa9d5 55%,var(--hero-deep) 100%)}
.banner{left:0;top:92px}
.intro{left:436px;top:145px;width:290px;text-align:center;color:var(--white);font-family:"Mulish",sans-serif;font-weight:800;font-size:24px;line-height:29px}
.intro em{font-style:normal;color:#45c8f2}
.intro-desc{left:502px;top:242px;width:180px;color:var(--white);font-size:16px;line-height:18px}
.search-box{left:183px;top:376px;width:793px;height:72px;background:rgba(23,60,95,.55)}
.field{position:absolute;top:18px;height:38px;background:var(--white);border-radius:3px;font-size:16px;color:#8a9098;padding:9px 16px}
.search-btn{position:absolute;left:652px;top:20px;width:114px;height:34px;background:var(--accent-blue);color:var(--white);font-family:"Mulish",sans-serif;font-weight:800;font-size:16px;text-align:center;line-height:34px;letter-spacing:1px}

/* video band */
.video-band{left:0;top:530px;width:1200px;height:190px;background:var(--green)}
.video-text{left:208px;top:556px;width:420px;color:var(--white);font-size:17px;line-height:17px}
.watch{left:403px;top:652px;width:166px;height:38px;border:2px solid var(--white);color:var(--white);font-size:20px;text-align:center;line-height:34px}
.thumb{left:714px;top:544px;width:237px;height:156px;background:linear-gradient(135deg,#cfe3f1,#8fb9d9)}

/* feature cards */
.paper{left:0;top:720px;width:1200px;height:405px;background:var(--paper)}
.card{position:absolute;top:768px;width:314px;height:295px;background:var(--white)}
.card .icon{position:absolute;left:14px;top:17px;width:82px;height:82px;border-radius:50%;border:4px solid #3a3f45;background:#f3f3f3}
.card h3{position:absolute;left:112px;top:34px;font-family:"Mulish",sans-serif;font-weight:700;font-size:21px;color:#3a3f45}
.card .sub{position:absolute;left:112px;top:60px;font-size:20px;color:#7b8189}
.card p{position:absolute;left:14px;top:110px;width:288px;font-size:13px;line-height:16.6px;color:var(--card-text);height:136px;overflow:hidden;text-align:justify}
.card .more{position:absolute;left:0;bottom:0;width:314px;height:40px;color:var(--white);font-size:20px;text-align:center;line-height:40px;background:var(--sky)}
.card .more.green{background:var(--green)}

/* about section */
.about{left:0;top:1121px;width:1200px;height:716px;background:var(--sky)}
.about-title{left:154px;top:1190px;font-family:"Mulish",sans-serif;font-weight:700;font-size:36px;color:var(--white)}
.row h4{position:absolute;left:287px;font-family:"Mulish",sans-serif;font-weight:800;font-size:23px;color:var(--white)}
.row p{position:absolute;left:287px;width:810px;font-size:15.5px;line-height:19.4px;color:var(--white);text-align:justify}
.row .pic{position:absolute;left:125px;width:145px;height:120px;background:rgba(255,255,255,.9);border-radius:6px}
.read-more{left:754px;top:1779px;width:338px;height:58px;background:var(--sky-dark);color:var(--white);font-size:46px;text-align:center;line-height:56px}

/* programs & degrees */
.programs{left:0;top:1837px;width:1200px;height:295px;background:var(--mid-blue)}
.col-head{font-family:"Mulish",sans-serif;font-weight:800;font-size:25px;color:var(--white)}
.list{list-style:none;font-size:15.5px;line-height:18.6px;color:var(--white)}
.divider{width:2px;height:170px;top:1930px;background:rgba(255,255,255,.6)}

/* states */
.states{left:0;top:2132px;width:1200px;height:245px;background:var(--deep-blue)}
.states-title{left:90px;top:2154px;font-family:"Mulish",sans-serif;font-weight:800;font-size:25px;color:var(--white)}
.state{position:absolute;width:117px;height:28px;background:var(--state-btn);color:var(--white);font-size:14px;text-align:center;line-height:28px}
.map{left:747px;top:2180px;width:416px;height:186px;background:linear-gradient(135deg,#8cbbe2,var(--map));border-radius:40px 60px 30px 80px}

/* footer */
.footer{left:0;top:2377px;width:1200px;height:85px;background:var(--green);color:var(--white);font-size:25px}
.footer span{position:absolute;top:22px;letter-spacing:1px}
</style>
</head>
<body>

<header class="abs topbar">
  <div class="abs brand">MY WEBSITE B\NAME</div>
  <nav class="nav">
    <a style="left:420px">Home</a>
    <a style="left:494px">States</a>
    <a style="left:571px">Programs</a>
    <a style="left:664px">Degrees</a>
    <a style="left:766px">Accreditation</a>
    <a style="left:891px">Rankings</a>
    <a style="left:988px">Resources</a>
  </nav>
  <div class="social">
    <span style="left:878px"></span><span style="left:922px"></span><span style="left:964px"></span><span style="left:1006px"></span>
  </div>
</header>

<section class="abs hero" role="img" aria-label="Graduates in caps and gowns tossing their hats against a blue sky"></section>
<svg class="abs banner" width="1200" height="438" viewBox="0 0 1200 438" aria-hidden="true">
  <path d="M436 0 H727 V180 L600 438 H560 L436 180 Z" fill="var(--banner)" opacity=".9"/>
  <rect x="492" y="0" width="180" height="18" fill="var(--accent-blue)"/>
</svg>
<div class="abs intro">Our website<br>intro <em>write it</em><br>Our website</div>
<p class="abs intro-desc">written description of the videowritten description of the the v the vvideowritten</p>
<div class="abs search-box">
  <div class="field" style="left:16px;width:409px">Search Collage</div>
  <div class="field" style="left:440px;width:195px">State</div>
  <div class="search-btn">SEARCH</div>
</div>

<section class="abs video-band"></section>
<p class="abs video-text">written description of the videowritten description of the videowritten description of the video written description of the video written description of the video written description of the video written description of the video</p>
<div class="abs watch">Watch video</div>
<svg class="abs" style="left:580px;top:640px" width="110" height="60" viewBox="0 0 110 60" aria-hidden="true">
  <path d="M6 18 Q30 52 92 28" fill="none" stroke="#fff" stroke-width="2.5"/>
  <path d="M78 14 L104 22 L86 40 Z" fill="none" stroke="#fff" stroke-width="2.5"/>
</svg>
<div class="abs thumb" role="img" aria-label="Video thumbnail of a student presenter">
  <svg width="237" height="156" viewBox="0 0 237 156" aria-hidden="true">
    <circle cx="108" cy="80" r="24" fill="var(--accent-blue)"/>
    <path d="M100 68 L122 80 L100 92 Z" fill="#fff"/>
  </svg>
</div>

<section class="abs paper"></section>
<article class="card" style="left:87px">
  <div class="icon" role="img" aria-label="Rankings icon"></div>
  <h3>Rankingsp</h3><div class="sub">explain small-desc</div>
  <p>One section with 3 Paragraphs of content (each paragraph around 100 words) with a header at the top. You can use placeholder text but please create the formatting. At the end of the 3 paragraphs please have a “Read More” Note this shouldn't be 3 separate paragraphs with three read mores - it is 3 paragraphs with one read more at the end.One section with 3 Paragraphs of content (each</p>
  <div class="more green">Read More</div>
</article>
<article class="card" style="left:424px">
  <div class="icon" role="img" aria-label="Accreditation icon"></div>
  <h3>Accreditation</h3><div class="sub">explain small-desc</div>
  <p>One section with 3 Paragraphs of content (each paragraph around 100 words) with a header at the top. You can use placeholder text but please create the formatting. At the end of the 3 paragraphs please have a “Read More” Note this shouldn't be 3 separate paragraphs with three read mores - it is 3 paragraphs with one read more at the end.One section with 3 Paragraphs of content (each</p>
  <div class="more">Read More</div>
</article>
<article class="card" style="left:764px">
  <div class="icon" role="img" aria-label="Resources icon"></div>
  <h3>Resources</h3><div class="sub">explain small-desc</div>
  <p>One section with 3 Paragraphs of content (each paragraph around 100 words) with a header at the top. You can use placeholder text but please create the formatting. At the end of the 3 paragraphs please have a “Read More” Note this shouldn't be 3 separate paragraphs with three read mores - it is 3 paragraphs with one read more at the end.One section with 3 Paragraphs of content (each</p>
  <div class="more">Read More</div>
</article>

<section class="abs about"></section>
<svg class="abs" style="left:0;top:1088px" width="1200" height="60" viewBox="0 0 1200 60" aria-hidden="true">
  <path d="M0 33 H500 C540 33 545 10 600 10 C655 10 660 33 700 33 H1200 V60 H0 Z" fill="var(--sky)"/>
  <path d="M590 56 H610 M600 46 V66" stroke="#5b6068" stroke-width="4" transform="translate(0,-14)"/>
</svg>
<h2 class="abs about-title">header at the top</h2>
<div class="row">
  <div class="pic" style="top:1272px" role="img" aria-label="Graduation cap illustration"></div>
  <h4 style="top:1283px">header at the top</h4>
  <p style="top:1316px">One section with 3 Paragraphs of content (each paragraph around 100 words) with a header at the top. You can use placeholder text but please create the formatting. At the end of the 3 paragraphs please have a “Read More” Note this shouldn't be 3 separate paragraphs with three read mores - it is 3 paragraphs with one read more at the end.One section with 3 Paragraphs of content (each paragraph around 100 words) with a header at the top. You can use placeholder text but please create the formatting. At the end of the 3 paragraphs please have a “Read More” Note this shouldn't be 3 separate paragraphs with three read mores - it is 3 paragraphs with one read more at</p>
</div>
<div class="row">
  <div class="pic" style="top:1455px" role="img" aria-label="Teacher at a board with students illustration"></div>
  <h4 style="top:1453px">header at the top</h4>
  <p style="top:1486px">One section with 3 Paragraphs of content (each paragraph around 100 words) with a header at the top. You can use placeholder text but please create the formatting. At the end of the 3 paragraphs please have a “Read More” Note this shouldn't be 3 separate paragraphs with three read mores - it is 3 paragraphs with one read more at the end.One section with 3 Paragraphs of content (each paragraph around 100 words) with a header at the top. You can use placeholder text but please create the formatting. At the end of the 3 paragraphs please have a “Read More” Note this shouldn't be 3 separate paragraphs with three read mores - it is 3 paragraphs with one read more at</p>
</div>
<div class="row">
  <div class="pic" style="top:1620px" role="img" aria-label="Open book illustration"></div>
  <h4 style="top:1623px">header at the top</h4>
  <p style="top:1656px">One section with 3 Paragraphs of content (each paragraph around 100 words) with a header at the top. You can use placeholder text but please create the formatting. At the end of the 3 paragraphs please have a “Read More” Note this shouldn't be 3 separate paragraphs with three read mores - it is 3 paragraphs with one read more at the end.One section with 3 Paragraphs of content (each paragraph around 100 words) with a header at the top. You can use placeholder text but please create the formatting. At the end of the 3 paragraphs please have a “Read More” Note this shouldn't be 3 separate paragraphs with three read mores - it is 3 paragraphs with one read more at</p>
</div>
<div class="abs read-more">Read More</div>

<section class="abs programs"></section>
<svg class="abs" style="left:560px;top:1837px" width="80" height="30" viewBox="0 0 80 30" aria-hidden="true">
  <path d="M22 0 L58 0 L40 22 Z" fill="#fff"/>
</svg>
<h3 class="abs col-head" style="left:108px;top:1880px">Programs</h3>
<h3 class="abs col-head" style="left:681px;top:1884px">Degrees</h3>
<ul class="abs list" style="left:112px;top:1926px"><li>Accounting</li><li>Art</li><li>Bible</li><li>Business</li><li>Criminal Justice</li><li>Design</li><li>Education</li><li>Engineering</li><li>English</li></ul>
<div class="abs divider" style="left:282px"></div>
<ul class="abs list" style="left:320px;top:1930px"><li>Accounting</li><li>Art</li><li>Bible</li><li>Business</li><li>Criminal Justice</li><li>Design</li><li>Education</li><li>Engineering</li><li>English</li></ul>
<div class="abs divider" style="left:471px"></div>
<ul class="abs list" style="left:500px;top:1937px"><li>Accounting</li><li>Art</li><li>Bible</li><li>Business</li><li>Criminal Justice</li><li>Design</li><li>Education</li><li>Engineering</li><li>English</li></ul>
<div class="abs divider" style="left:656px"></div>
<ul class="abs list" style="left:685px;top:1936px"><li>Accounting</li><li>Art</li><li>Bible</li><li>Business</li><li>Criminal Justice</li><li>Design</li><li>Education</li><li>Engineering</li><li>English</li></ul>
<div class="abs divider" style="left:843px"></div>
<ul class="abs list" style="left:874px;top:1936px"><li>Accounting</li><li>Art</li><li>Bible</li><li>Business</li><li>Criminal Justice</li><li>Design</li><li>Education</li><li>Engineering</li><li>English</li></ul>

<section class="abs states"></section>
<svg class="abs" style="left:90px;top:2160px" width="24" height="24" viewBox="0 0 24 24" aria-hidden="true">
  <circle cx="10" cy="10" r="7" fill="none" stroke="#fff" stroke-width="3"/><path d="M15 15 L22 22" stroke="#fff" stroke-width="3.5"/>
</svg>
<h3 class="abs states-title" style="left:120px">Colleges by State</h3>
<div class="abs" style="left:0;top:0">
  <span class="state" style="left:85px;top:2213px">state</span><span class="state" style="left:212px;top:2213px">state</span><span class="state" style="left:340px;top:2213px">state</span><span class="state" style="left:469px;top:2213px">state</span><span class="state" style="left:598px;top:2213px">state</span>
  <span class="state" style="left:85px;top:2254px">state</span><span class="state" style="left:212px;top:2254px">state</span><span class="state" style="left:340px;top:2254px">state</span><span class="state" style="left:469px;top:2254px">state</span><span class="state" style="left:598px;top:2254px">state</span>
  <span class="state" style="left:85px;top:2294px">state</span><span class="state" style="left:212px;top:2294px">state</span><span class="state" style="left:340px;top:2294px">state</span><span class="state" style="left:469px;top:2294px">state</span><span class="state" style="left:598px;top:2294px">state</span>
  <span class="state" style="left:85px;top:2336px">state</span><span class="state" style="left:212px;top:2336px">state</span><span class="state" style="left:340px;top:2336px">state</span><span class="state" style="left:469px;top:2336px">state</span><span class="state" style="left:598px;top:2336px">state</span>
</div>
<div class="abs map" role="img" aria-label="Map of the United States divided by state"></div>

<footer class="abs footer">
  <span style="left:73px">copyright@www.url.com</span>
  <span style="left:789px">about us</span>
  <span style="left:928px">privacy</span>
</footer>

</body>
</html>
```